Computer consultant business card

Bexil Software is a newly started computer consulting company. It's a small one-man company that provides mostly Vornix applications but also websites in collaboration with designers. I'm running this company on the side of full time university studies.

I want the final design to be clean and memorable. Be creative! :)

Some inspiration:
http://www.pixelmarta.com/design/48317
http://www.pixelmarta.com/design/2739164/business-card-design-by-frostlynk
http://www.pixelmarta.com/design/604281/business-card-design-by-koralind-vestrabanu

See attachment for my company logo.
Updates

I would like to thank everyone for submitting! I'll need a couple of days to review and ultimately select a design.

Target Market(s)

Non-technical entrepreneurs and small companies.

Industry/Entity Type

University

Requirements
Must have
• My company logo.
In any way, both colors from my logo.
First- and last name, e-mail and phone number.
Double-sided design.
Nice to have
• Something creative with the symbol in my logo

```html
<!DOCTYPE html>
<html lang="en">
<head>
<meta charset="utf-8">
<title>Xelvor – Business Card</title>
<link href="https://fonts.googleapis.com/css2?family=Open+Sans:wght@400;600;700&display=swap" rel="stylesheet">
<style>
  :root {
    --stage: #e9e6e1;
    --ink: #333335;
    --ink-soft: #4a4a4c;
    --brand-blue: #4472b8;
    --paper: #ffffff;
    --night: #050505;
    --slate: #2f3038;
    --slate-glow: #4a5a82;
    --label: #1d1d1d;
  }
  * { margin: 0; padding: 0; box-sizing: border-box; }
  html, body {
    width: 1200px; height: 788px; overflow: hidden;
    background: var(--stage);
    font-family: "Open Sans", Arial, sans-serif;
  }
  .sheet { position: relative; width: 1200px; height: 788px; }

  .view-label {
    position: absolute; width: 525px; text-align: center;
    font-size: 20px; color: var(--label); font-weight: 400;
  }
  .card {
    position: absolute; width: 525px; height: 299px;
    border-radius: 20px; overflow: hidden;
    box-shadow: 0 4px 10px rgba(0,0,0,.25);
  }

  /* brand mark: plain circle + name */
  .brand { position: absolute; display: flex; align-items: center; }
  .brand-dot { border-radius: 50%; background: var(--brand-blue); flex: none; }
  .brand-name { font-weight: 600; letter-spacing: 0; line-height: 1; }

  /* front */
  .card-front { left: 57px; top: 75px; background: var(--paper); }
  .card-front .brand { left: 40px; top: 36px; gap: 20px; }
  .card-front .brand-dot { width: 62px; height: 62px; }
  .card-front .brand-name { font-size: 46px; color: var(--ink); }
  .swoosh { position: absolute; inset: 0; }
  .holder { position: absolute; left: 43px; top: 178px; color: var(--ink); }
  .holder-name { font-size: 17px; font-weight: 700; }
  .holder-role { font-size: 12px; color: var(--ink-soft); margin-top: 1px; }
  .contact {
    position: absolute; right: 33px; top: 242px; text-align: right;
    color: var(--paper); font-size: 14px; line-height: 21px;
  }
  .contact b { font-style: italic; font-weight: 700; }

  /* backs */
  .card-back .brand { left: 0; right: 0; justify-content: center; top: 95px; gap: 28px; }
  .card-back .brand-dot { width: 100px; height: 100px; }
  .card-back .brand-name { font-size: 66px; }
  .web {
    position: absolute; left: 0; right: 0; text-align: center;
    font-size: 17px; letter-spacing: 4px;
  }

  .card-back-light { left: 622px; top: 75px; background: var(--paper); }
  .card-back-light .brand-name { color: var(--ink); }
  .card-back-light .web { top: 248px; color: var(--ink-soft); }

  .card-back-dark { left: 54px; top: 446px; background: var(--night); }
  .card-back-dark .brand-name, .card-back-dark .web { color: var(--paper); }
  .card-back-dark .web { top: 254px; }
  .texture {
    position: absolute; inset: 0;
    background:
      radial-gradient(ellipse 170px 90px at 150px 20px, rgba(90,90,95,.45), transparent 70%),
      radial-gradient(ellipse 160px 110px at 420px 290px, rgba(110,105,110,.45), transparent 70%);
  }

  .card-back-slate {
    left: 622px; top: 446px;
    background: radial-gradient(ellipse 420px 260px at 50% 110%, var(--slate-glow), var(--slate) 75%);
  }
  .card-back-slate .brand-name, .card-back-slate .web { color: var(--paper); }
  .card-back-slate .web { top: 254px; }
</style>
</head>
<body>
<main class="sheet">
  <p class="view-label" style="left:57px;top:34px">Front</p>
  <p class="view-label" style="left:622px;top:34px">Back - 1</p>
  <p class="view-label" style="left:54px;top:404px">Back - 2</p>
  <p class="view-label" style="left:622px;top:404px">Back - 3</p>

  <section class="card card-front">
    <svg class="swoosh" viewBox="0 0 525 299" width="525" height="299" aria-hidden="true">
      <path d="M0,262 C180,284 380,222 525,112 L525,299 L0,299Z" fill="var(--brand-blue)"/>
      <path d="M0,269 C190,290 390,236 525,150 L525,299 L0,299Z" fill="var(--paper)"/>
      <path d="M0,273 C200,293 400,246 525,158 L525,299 L0,299Z" fill="var(--ink)"/>
    </svg>
    <div class="brand">
      <span class="brand-dot"></span>
      <span class="brand-name">xelvor</span>
    </div>
    <div class="holder">
      <p class="holder-name">First Name Last Name</p>
      <p class="holder-role">Designation</p>
    </div>
    <div class="contact">
      <p><b>p</b> : +12 345 6789</p>
      <p><b>e</b> : info@xelvor-apps.net</p>
    </div>
  </section>

  <section class="card card-back card-back-light">
    <div class="brand">
      <span class="brand-dot"></span>
      <span class="brand-name">xelvor</span>
    </div>
    <p class="web">www.xelvor-apps.net</p>
  </section>

  <section class="card card-back card-back-dark">
    <div class="texture" role="img" aria-label="Perforated metal dot texture in the corners"></div>
    <div class="brand">
      <span class="brand-dot"></span>
      <span class="brand-name">xelvor</span>
    </div>
    <p class="web">www.xelvor-apps.net</p>
  </section>

  <section class="card card-back card-back-slate">
    <div class="brand">
      <span class="brand-dot"></span>
      <span class="brand-name">xelvor</span>
    </div>
    <p class="web">www.xelvor-apps.net</p>
  </section>
</main>
</body>
</html>
```